Velmor Spire Nine Flash website

we need a website to cater to 2 aspect of the business. We have Velmor spire residence and velmor spire office. For the office, we will get their inquire and arrange a face to face meetup to show them the office area for rent. For the residence side, it will need to be like staylane or roomvio.com. we want to allow them to book online for the date they need. We have a total of 10 different room configurations starting at $70 per night and up depending on the size of the room. example of the design is https://brisquelodge.com/

Target Market(s)

the website should have detail information on the layout, designs, and luxury of the building.

Industry/Entity Type

office and service appartment rental/lease

Coding

Coded - Design and coding required

Number of Pages Required

5+ page

Requirements
Must have
• a luxury perspective
Nice to have
• example https://brisquelodge.com/

```html
<!DOCTYPE html>
<html lang="en">
<head>
<meta charset="utf-8">
<title>Velmor Spire Nine</title>
<link href="https://fonts.googleapis.com/css2?family=Cinzel:wght@400;600&family=Open+Sans:wght@400;600;700&display=swap" rel="stylesheet">
<style>
:root{
  --stage:#8c8c8c;
  --paper:#ffffff;
  --paper-warm:#fbf7ef;
  --gold:#e8991c;
  --gold-light:#f4b431;
  --gold-dark:#d9820f;
  --ink:#2b2b2b;
  --charcoal:#3b3b3b;
  --text:#555555;
  --muted:#8a8a8a;
  --line:#e3e3e3;
}
*{box-sizing:border-box;margin:0;padding:0}
html,body{width:1200px;height:4380px;overflow:hidden}
body{background:var(--stage);font-family:"Open Sans",Arial,sans-serif;color:var(--text);position:relative}
.panel{position:absolute;left:96px;width:1008px;background:var(--paper);overflow:hidden}
.abs{position:absolute}
.serif{font-family:"Cinzel",Georgia,serif}
.brand-mark{display:inline-block;background:var(--gold)}
.btn{position:absolute;display:flex;align-items:center;justify-content:center;gap:8px;font-size:11px;font-weight:700;letter-spacing:.5px;color:#fff;text-transform:uppercase;white-space:nowrap}
.btn-gold{background:linear-gradient(90deg,var(--gold-dark),var(--gold-light))}
.btn-dark{background:var(--charcoal)}
.photo{position:absolute}
.backdrop{position:absolute;left:0;width:1008px;background:
  radial-gradient(ellipse at 10% 30%,rgba(232,153,28,.07),transparent 55%),
  radial-gradient(ellipse at 90% 70%,rgba(232,153,28,.07),transparent 55%),
  linear-gradient(180deg,var(--paper),var(--paper-warm))}

/* splash */
.splash{top:0;height:712px}
.splash .brand-mark{position:absolute;left:454px;top:150px;width:100px;height:110px}
.splash .brand-name{position:absolute;left:0;width:100%;top:330px;text-align:center;font-size:40px;color:var(--text);font-family:"Cinzel",Georgia,serif}

/* home */
.home{top:780px;height:3520px}
.nav{position:absolute;top:0;left:0;width:100%;height:80px;display:flex;align-items:center;padding:0 32px;background:#fff;z-index:2}
.nav .brand{display:flex;align-items:center;gap:10px;font-family:"Cinzel",Georgia,serif;font-size:22px;color:var(--text)}
.nav .brand .brand-mark{width:22px;height:24px}
.nav ul{list-style:none;display:flex;gap:34px;margin-left:auto;margin-right:20px}
.nav li{font-size:11px;font-weight:600;color:var(--ink);padding-bottom:6px;border-bottom:2px solid transparent}
.nav li.active{border-bottom-color:var(--gold)}
.hero{top:80px;left:0;width:1008px;height:508px;background:
  linear-gradient(180deg,rgba(255,255,255,0) 62%,rgba(70,76,82,.55) 100%),
  linear-gradient(90deg,#141a22 0%,#26303b 18%,#4a5560 30%,#c7cfd6 42%,#f2f4f6 58%,#e6eaee 75%,#b9c2ca 100%)}
.hero h1{position:absolute;left:40px;top:150px;font-family:"Cinzel",Georgia,serif;font-weight:400;font-size:50px;line-height:56px;color:#fff}
.hero .rule{position:absolute;left:40px;top:274px;width:170px;height:3px;background:var(--gold)}
.section-title{position:absolute;left:0;width:100%;text-align:center;font-family:"Cinzel",Georgia,serif;font-size:30px;color:var(--ink)}
.card{position:absolute;width:260px;height:276px;background:#fff;box-shadow:0 2px 10px rgba(0,0,0,.12)}
.card .photo{left:0;top:0;width:260px;height:160px}
.card h3{position:absolute;left:0;width:100%;top:178px;text-align:center;font-size:15px;font-weight:700;color:var(--ink)}
.card p{position:absolute;left:30px;right:30px;top:204px;text-align:center;font-size:10px;line-height:14px;color:var(--muted)}
.card.featured{background:var(--gold);height:256px}
.card.featured h3,.card.featured p{color:#fff}
.about-box{position:absolute;left:104px;top:1380px;width:760px;height:300px;background:#fff;box-shadow:0 4px 20px rgba(0,0,0,.15);text-align:center;z-index:1}
.about-box .brand-mark{position:absolute;left:366px;top:26px;width:28px;height:30px}
.about-box h2{position:absolute;left:0;width:100%;top:70px;font-family:"Cinzel",Georgia,serif;font-weight:400;font-size:30px;color:var(--ink)}
.about-box p{position:absolute;left:80px;right:80px;top:124px;font-size:13px;line-height:22px;color:var(--text)}
.bracket{position:absolute;left:84px;top:1360px;width:90px;height:90px;border-top:6px solid var(--gold);border-left:6px solid var(--gold);z-index:1}
.blog-date{font-size:11px;color:var(--text);margin-bottom:8px}
.blog-text{font-size:13px;font-weight:700;line-height:19px;color:var(--ink)}
.blog-more{display:inline-block;margin-top:8px;font-size:10px;font-weight:700;color:var(--gold);border-bottom:1px solid var(--gold)}
.contact{top:2740px;left:0;width:1008px;height:420px;background:linear-gradient(180deg,var(--gold-light),var(--gold-dark))}
.contact h2{position:absolute;top:46px;width:100%;text-align:center;font-family:"Cinzel",Georgia,serif;font-weight:400;font-size:30px;color:#fff}
.field{position:absolute;background:#fff;font-size:11px;color:var(--muted);padding:10px 14px;border:1px solid #f0d7a8}
.footer{top:3160px;left:0;width:1008px;height:360px;background:var(--ink);color:#cfcfcf}
.footer h4{font-family:"Cinzel",Georgia,serif;font-weight:400;font-size:15px;color:#fff;margin-bottom:14px}
.footer li{list-style:none;font-size:11px;line-height:22px}
.footer .col{position:absolute;top:66px}
.contact-row{display:flex;gap:10px;align-items:flex-start;font-size:11px;line-height:15px;margin-bottom:14px}
.dot{width:18px;height:18px;border-radius:50%;background:var(--gold);display:flex;align-items:center;justify-content:center;flex:none}
.social{position:absolute;top:316px;width:20px;height:20px;border-radius:50%;border:1px solid #bbb}
</style>
</head>
<body>

<section class="panel splash">
  <div class="backdrop" style="top:0;height:712px"></div>
  <span class="brand-mark"></span>
  <div class="brand-name">Velmor Spire Nine</div>
  <div class="btn btn-dark" style="left:288px;top:408px;width:208px;height:50px">Velmor Spire Residence ›</div>
  <div class="btn btn-gold" style="left:504px;top:408px;width:212px;height:50px">Velmor Spire Office ›</div>
</section>

<main class="panel home">
  <div class="backdrop" style="top:588px;height:2152px"></div>
  <header class="nav">
    <div class="brand"><span class="brand-mark"></span>Velmor Spire Nine</div>
    <ul>
      <li class="active">ABOUT US</li><li>OFFICE SPACE</li><li>BLOGS</li><li>GALLERY</li><li>WHY US</li><li>CONTACT US</li>
    </ul>
  </header>

  <section class="photo hero" role="img" aria-label="Bright modern open-plan office with desks and large windows">
    <h1>FIND BEST<br>OFFICE SPACE</h1>
    <div class="rule"></div>
    <div class="btn btn-gold" style="left:40px;top:300px;width:130px;height:32px">Contact Us ›</div>
  </section>

  <h2 class="section-title" style="top:625px">OFFICE SPACE LISTINGS</h2>

  <article class="card" style="left:92px;top:700px"><div class="photo" role="img" aria-label="Office interior with white desks" style="background:linear-gradient(180deg,#f4f6f8 0%,#dfe5ea 50%,#8f9aa4 100%)"></div><h3>Office Space Title</h3><p>Lorem ipsum dolor sit amet, consectetur adipiscing elit, sed do eiusmod tempor.</p></article>
  <article class="card featured" style="left:372px;top:700px"><div class="photo" role="img" aria-label="Office interior with blue glass walls" style="background:linear-gradient(180deg,#c9dcec 0%,#8fb0cc 55%,#4d6a85 100%)"></div><h3>Office Space Title</h3><p>Lorem ipsum dolor sit amet, consectetur adipiscing elit, sed do eiusmod tempor.</p></article>
  <article class="card" style="left:652px;top:700px"><div class="photo" role="img" aria-label="Office interior with pendant lights" style="background:linear-gradient(180deg,#fafafa 0%,#e9ebed 55%,#b4bcc3 100%)"></div><h3>Office Space Title</h3><p>Lorem ipsum dolor sit amet, consectetur adipiscing elit, sed do eiusmod tempor.</p></article>
  <article class="card" style="left:92px;top:1012px"><div class="photo" role="img" aria-label="Office interior with orange accents" style="background:linear-gradient(160deg,#e3edf5 0%,#9fbbd3 50%,#e59a3a 100%)"></div><h3>Office Space Title</h3><p>Lorem ipsum dolor sit amet, consectetur adipiscing elit, sed do eiusmod tempor.</p></article>
  <article class="card" style="left:372px;top:1012px"><div class="photo" role="img" aria-label="Office interior with dark window frames" style="background:linear-gradient(180deg,#e5eaee 0%,#7c8892 50%,#2e353c 100%)"></div><h3>Office Space Title</h3><p>Lorem ipsum dolor sit amet, consectetur adipiscing elit, sed do eiusmod tempor.</p></article>
  <article class="card" style="left:652px;top:1012px"><div class="photo" role="img" aria-label="Office interior with city view" style="background:linear-gradient(180deg,#f1f4f6 0%,#c5ced6 55%,#5a6670 100%)"></div><h3>Office Space Title</h3><p>Lorem ipsum dolor sit amet, consectetur adipiscing elit, sed do eiusmod tempor.</p></article>

  <div class="photo" role="img" aria-label="Office floor with chairs and city skyline through windows" style="left:0;top:1600px;width:1008px;height:440px;background:linear-gradient(180deg,#eef1f3 0%,#d3dbe1 30%,#a7b2bb 50%,#5d666d 68%,#2f3438 85%,#8b8f92 100%)"></div>
  <div class="bracket"></div>
  <section class="about-box">
    <span class="brand-mark"></span>
    <h2>ABOUT VELMOR SPIRE OFFICE</h2>
    <p>Lorem ipsum dolor sit amet, consectetur adipiscing elit, sed do eiusmod tempor incididunt ut labore et dolore magna aliqua. Ut enim ad minim veniam, quis nostrud exercitation ullamco laboris nisi ut aliquip ex ea commodo consequat. Duis aute irure dolor in reprehenderit in voluptate velit.</p>
    <div class="btn btn-gold" style="left:320px;top:246px;width:120px;height:30px">Learn More ›</div>
  </section>

  <h2 class="section-title" style="top:2080px;text-align:left;left:92px">LATEST BLOGS</h2>
  <div class="photo" role="img" aria-label="Office lounge with chairs" style="left:96px;top:2160px;width:280px;height:310px;background:linear-gradient(180deg,#3a3a38 0%,#f3efe6 28%,#e2d8c6 60%,#8d7f6c 100%)"></div>
  <div class="abs" style="left:96px;top:2490px;width:280px">
    <div class="blog-date">02 JUNE 2023</div>
    <div class="blog-text">Lorem ipsum dolor sit amet, consectetur adipiscing elit, sed do eiusmod tempor incididunt ut labore et</div>
    <span class="blog-more">LEARN MORE</span>
  </div>
  <div class="photo" role="img" aria-label="Open office with ceiling lights" style="left:404px;top:2160px;width:260px;height:160px;background:linear-gradient(180deg,#f5f6f7 0%,#dfe3e6 50%,#8b949b 100%)"></div>
  <div class="abs" style="left:676px;top:2180px;width:240px">
    <div class="blog-date">02 JUNE 2023</div>
    <div class="blog-text">Lorem ipsum dolor sit amet, consectetur adipiscing elit, sed do eiusmod tempor incididunt ut labore et</div>
    <span class="blog-more">LEARN MORE</span>
  </div>
  <div class="photo" role="img" aria-label="Office workspace with desks and plants" style="left:404px;top:2336px;width:260px;height:164px;background:linear-gradient(160deg,#c4d3dd 0%,#6f8290 50%,#3c4a40 100%)"></div>
  <div class="abs" style="left:676px;top:2360px;width:240px">
    <div class="blog-date">02 JUNE 2023</div>
    <div class="blog-text">Lorem ipsum dolor sit amet, consectetur adipiscing elit, sed do eiusmod tempor incididunt ut labore et</div>
    <span class="blog-more">LEARN MORE</span>
  </div>
  <div class="abs" style="left:404px;top:2520px;width:512px;height:1px;background:var(--line)"></div>
  <div class="btn btn-gold" style="left:432px;top:2555px;width:144px;height:32px">View All Blogs</div>

  <section class="abs contact">
    <h2>CONTACT US</h2>
    <div class="field" style="left:192px;top:104px;width:312px;height:38px">First Name</div>
    <div class="field" style="left:504px;top:104px;width:312px;height:38px">Last Name</div>
    <div class="field" style="left:192px;top:142px;width:312px;height:38px">Phone number</div>
    <div class="field" style="left:504px;top:142px;width:312px;height:38px">Email address</div>
    <div class="field" style="left:192px;top:180px;width:624px;height:130px">Message</div>
    <div class="btn" style="left:448px;top:332px;width:112px;height:34px;background:#111">SEND NOW</div>
  </section>

  <footer class="abs footer">
    <div class="abs" style="left:142px;top:66px;width:60px;height:66px;background:var(--gold)"></div>
    <div class="abs serif" style="left:52px;top:150px;width:240px;text-align:center;font-size:20px;color:var(--gold);white-space:nowrap">Velmor Spire Nine</div>
    <div class="col" style="left:416px"><h4>Navigation</h4><ul><li>Home</li><li>About</li><li>Office Space</li><li>Testimonials</li></ul></div>
    <div class="col" style="left:568px"><h4>Resources</h4><ul><li>Gallery</li><li>Blogs</li><li>Contact Us</li></ul></div>
    <div class="col" style="left:720px"><h4>Contact Us</h4>
      <div class="contact-row"><span class="dot"><svg width="10" height="10" viewBox="0 0 24 24"><path fill="#fff" d="M6.6 10.8a15 15 0 0 0 6.6 6.6l2.2-2.2c.3-.3.7-.4 1-.2 1.1.4 2.3.6 3.6.6.6 0 1 .4 1 1V20c0 .6-.4 1-1 1C10.6 21 3 13.4 3 4c0-.6.4-1 1-1h3.5c.6 0 1 .4 1 1 0 1.3.2 2.5.6 3.6.1.3 0 .7-.2 1z"/></svg></span><span>Phone Number<br>(555) 014-2290</span></div>
      <div class="contact-row"><span class="dot"><svg width="10" height="10" viewBox="0 0 24 24"><path fill="#fff" d="M3 5h18v14H3zM3 5l9 7 9-7" stroke="#e8991c" stroke-width="1.5"/></svg></span><span>Email address<br>hello@velmorspire.com</span></div>
    </div>
    <div class="abs" style="left:92px;top:300px;width:824px;height:1px;background:#555"></div>
    <div class="abs" style="left:92px;top:318px;font-size:9px;color:#9a9a9a">© 2023 Velmor Spire Nine. All Rights Reserved.</div>
    <span class="social" style="left:848px"></span><span class="social" style="left:872px"></span><span class="social" style="left:896px"></span>
  </footer>
</main>

</body>
</html>
```